Whitcombe Business Card Design

The name of the business is Dario Whitcombe, CPA LLC
The service that we offer is Accounting, Tax & Consulting Services. I need it to have the following items:
Dario Whitcombe, Principal
Phone Number
Email Address
Physical Address

I have attached the company logo, one in black and one in white. Please provide a design in black background and the other in white background. Please include "Accounting, Tax & Consulting Services". I want the business card to be clean and very professional.

```html
<!DOCTYPE html>
<html lang="en">
<head>
<meta charset="utf-8">
<title>Dario Whitcombe, CPA LLC – Business Card</title>
<link rel="stylesheet" href="https://fonts.googleapis.com/css2?family=Montserrat:wght@500;600&family=Roboto:wght@400;500;700&display=swap">
<style>
  :root {
    --backdrop: #d9d9d9;
    --card: #000000;
    --band: #4a4a4c;
    --band-text: #c4c4c6;
    --name-grey: #8c8c8f;
    --light-grey: #c9c9cb;
    --accent-red: #b01e23;
  }
  * { box-sizing: border-box; margin: 0; padding: 0; }
  html, body {
    width: 1200px; height: 900px; overflow: hidden;
    background: var(--backdrop);
  }
  .canvas { position: relative; width: 1200px; height: 900px; }
  .card {
    position: absolute; left: 233px; width: 705px;
    background: var(--card);
    box-shadow: 0 6px 18px rgba(0,0,0,0.25);
    overflow: hidden;
  }
  .card--front { top: 43px; height: 403px; }
  .card--back { top: 457px; height: 403px; }

  .service-band {
    position: absolute; left: 0; width: 100%; height: 44px;
    background: var(--band);
    display: flex; align-items: center; justify-content: center;
    font-family: "Roboto", sans-serif; font-weight: 700;
    font-size: 17px; letter-spacing: 0.36em; color: var(--band-text);
    text-transform: uppercase; padding-left: 0.36em;
  }
  .card--front .service-band { top: 194px; }
  .card--back .service-band { top: 359px; }

  .wordmark {
    position: absolute; left: 0; width: 100%; text-align: center;
    font-family: "Montserrat", sans-serif; text-transform: uppercase;
    line-height: 1.1;
  }
  .wordmark__name {
    display: inline-flex; align-items: center; gap: 12px;
    font-weight: 500; color: var(--name-grey);
  }
  .wordmark__square { display: inline-block; background: var(--accent-red); }
  .wordmark__tagline { font-weight: 600; color: var(--light-grey); }

  .card--front .wordmark { top: 264px; }
  .card--front .wordmark__name { font-size: 37px; }
  .card--front .wordmark__square { width: 24px; height: 24px; }
  .card--front .wordmark__tagline {
    display: block; margin-top: 6px; font-size: 31px; letter-spacing: 0.07em;
  }

  .card--back .wordmark { top: 264px; left: 405px; width: 268px; }
  .card--back .wordmark__name { font-size: 15.5px; gap: 7px; }
  .card--back .wordmark__square { width: 10px; height: 10px; }
  .card--back .wordmark__tagline {
    display: block; margin-top: 3px; font-size: 12.5px; letter-spacing: 0.08em;
  }

  .person {
    position: absolute; left: 44px; top: 50px;
    font-family: "Roboto", sans-serif;
  }
  .person__name { font-size: 31px; font-weight: 500; color: var(--light-grey); }
  .person__role { font-size: 19px; color: var(--accent-red); margin-top: 1px; }

  .contact-list {
    position: absolute; left: 44px; top: 150px; list-style: none;
    font-family: "Roboto", sans-serif; font-size: 22.5px; color: var(--light-grey);
  }
  .contact-item { display: flex; align-items: flex-start; gap: 22px; margin-bottom: 19px; line-height: 27px; }
  .contact-icon { width: 20px; height: 27px; flex: none; }
</style>
</head>
<body>
<main class="canvas">

  <section class="card card--front" aria-label="Card front">
    <div class="service-band">Accounting, Tax &amp; Consulting Services</div>
    <div class="wordmark">
      <span class="wordmark__name"><span class="wordmark__square"></span>Dario Whitcombe, CPA, LLC</span>
      <span class="wordmark__tagline">Certified Public Accountant</span>
    </div>
  </section>

  <section class="card card--back" aria-label="Card back">
    <div class="person">
      <h1 class="person__name">Dario Whitcombe</h1>
      <p class="person__role">Principal</p>
    </div>

    <ul class="contact-list">
      <li class="contact-item">
        <svg class="contact-icon" viewBox="0 0 20 27" aria-hidden="true">
          <path d="M10 3a6.5 6.5 0 0 0-6.5 6.5C3.5 14.5 10 21 10 21s6.5-6.5 6.5-11.5A6.5 6.5 0 0 0 10 3zm0 9a2.5 2.5 0 1 1 0-5 2.5 2.5 0 0 1 0 5z" fill="#b01e23"/>
        </svg>
        <span>421, Address line goes here<br>45552, Country Name</span>
      </li>
      <li class="contact-item">
        <svg class="contact-icon" viewBox="0 0 20 27" aria-hidden="true">
          <path d="M5 6c1-.6 2-.4 2.5.4l1.4 2.4c.4.7.2 1.5-.4 2l-1 .7c.8 1.8 2.2 3.3 4 4.2l.8-1c.5-.6 1.3-.8 2-.4l2.3 1.4c.8.5 1 1.5.4 2.4l-.8 1.2c-.6.8-1.7 1.1-2.7.7C8.4 18.4 4.8 14.5 3.5 9.4 3.2 8.3 3.7 7.1 4.6 6.4z" fill="#b01e23"/>
        </svg>
        <span>(555) 214-0387</span>
      </li>
      <li class="contact-item">
        <svg class="contact-icon" viewBox="0 0 20 27" aria-hidden="true">
          <rect x="1" y="8" width="18" height="12" fill="#b01e23"/>
          <path d="M1.5 8.5 10 15l8.5-6.5" fill="none" stroke="#000" stroke-width="1.4"/>
        </svg>
        <span>info@whitcombe.com</span>
      </li>
    </ul>

    <div class="wordmark">
      <span class="wordmark__name"><span class="wordmark__square"></span>Dario Whitcombe, CPA, LLC</span>
      <span class="wordmark__tagline">Certified Public Accountant</span>
    </div>

    <div class="service-band">Accounting, Tax &amp; Consulting Services</div>
  </section>

</main>
</body>
</html>
```